Business Card - high end, modern health care

Hey designers!

We need a double sided business card for the boutique, cutting edge physical therapy rehabilitation centre in Sydney's Northern Beaches.

With the most qualified physios in the area The Harbourview Motion Clinic does what other physiotherapy practices do not, we take our time with our patients giving them longer appointments, better physios and therefor faster results!

We guarantee that the service people receive at THMC will be unparalleled.

Hence we need a business card to reflect our modern, boutique, high end service. The final design needs to reflect that we are in a class of our own yet with the feel of beachside retreat.

Below I have attached our logo in both blue on white and white on blue. The exact colour is;
and the font that we have used in our logo is Tex Gyre Aventador.

I like the idea of the blue as the main colour as it is more eye catching and our signage onto the main road will be in this blue and in the interest of consistency across marketing the blue needs to be a part of the design. However I would appreciate a few designs onto a wooden background as this is a visual theme within the fitout of the practice.

The design needs to be of standard size (91x55mm).

Target Market(s)

We target people who have an end outcome in mind and those who have had poor experiences with other providers and ensure that everyone gets the care that they deserve with a premium service that is tailored to the individuals circumstances. As a premium service, the target market is highly educated, business and tech savvy with the additional target market of elderly people who have self funded their retirement and see value in paying for the best ongoing rehabilitation to maintain independence.

Industry/Entity Type

Physical Therapy

Contact Information for Business Card

Name, designation( Titled Musculoskeletal Physiotherapist... there will also be those in the company that have multiple designations ie 5 or 6 words long), phone number, email, facebook, instagram, address

Font styles to use
Sans Serif

Colors

Designer to choose colors to be used in the design.

Requirements
Must have
• Front - The logo as large as possible, blue or wooden theme, and all of the important details.
• Back - A blank space/lines on which to write appointment times (no "Appointment, date, time" etc.)
Nice to have
• facebook url
• logos for facebook and instagram
• Mini logos for the phone and email?

```html
<!DOCTYPE html>
<html lang="en">
<head>
<meta charset="utf-8">
<title>The Harbourview Motion Clinic – Business Card</title>
<link rel="stylesheet" href="https://fonts.googleapis.com/css2?family=Roboto:wght@400;500;700&family=Roboto+Condensed:wght@700&family=PT+Sans&display=swap">
<style>
  :root {
    --brand-blue: #0d56a6;
    --rule-blue: #4a8fd6;
    --text-grey: #555555;
    --line-grey: #6a6a6a;
    --card-white: #f4f4f4;
    --back-white: #ffffff;
    --faint-mark: #eef2f7;
    --stage: #2a2a2a;
  }
  * { margin: 0; padding: 0; box-sizing: border-box; }
  html, body { width: 1200px; height: 960px; overflow: hidden; }
  body { background: var(--stage); position: relative; font-family: 'Roboto', Arial, sans-serif; }

  .card { position: absolute; width: 598px; height: 342px; border-radius: 18px; overflow: hidden; }
  .card-front { left: 322px; top: 108px; background: var(--card-white); }
  .card-back { left: 320px; top: 493px; width: 600px; background: var(--back-white); font-family: 'PT Sans', Arial, sans-serif; }

  .brand { position: absolute; right: 28px; top: 40px; display: flex; align-items: center; gap: 8px; }
  .brand-dot { width: 46px; height: 46px; border-radius: 50%; background: var(--brand-blue); }
  .brand-name { color: var(--brand-blue); font-weight: 700; font-size: 21px; line-height: 22px; letter-spacing: 0.5px; }

  .person { position: absolute; left: 28px; top: 175px; }
  .person-name { font-family: 'Roboto Condensed', Arial, sans-serif; font-weight: 700; font-size: 21px; color: var(--brand-blue); }
  .person-title { font-weight: 500; font-size: 15px; color: var(--text-grey); margin-top: 1px; }

  .divider { position: absolute; left: 28px; right: 32px; top: 225px; height: 1px; background: var(--rule-blue); }

  .contacts { position: absolute; left: 30px; top: 234px; list-style: none; font-size: 14px; color: var(--text-grey); }
  .contacts li { display: flex; align-items: center; height: 19px; }
  .contacts svg { width: 13px; height: 13px; margin-right: 9px; fill: var(--brand-blue); }

  .address { position: absolute; right: 28px; top: 257px; text-align: right; font-size: 14px; line-height: 19px; color: var(--text-grey); }

  .base-band { position: absolute; left: 0; right: 0; bottom: 0; height: 13px; background: var(--brand-blue); border-top: 3px solid #d8d8d8; }

  .faint-mark { position: absolute; left: 150px; top: 30px; width: 300px; height: 300px; border-radius: 50%; background: var(--faint-mark); }

  .slot { position: absolute; left: 32px; right: 42px; display: flex; align-items: flex-end; font-size: 16px; color: var(--line-grey); }
  .slot-row-1 { top: 39px; }
  .slot-row-2 { top: 83px; }
  .slot .blank { border-bottom: 1px solid var(--line-grey); margin: 0 6px 5px 4px; }
  .slot .blank-date { width: 262px; }
  .slot .blank-time { width: 114px; }
  .write-line { position: absolute; left: 35px; right: 42px; height: 1px; background: var(--line-grey); }
</style>
</head>
<body>

<section class="card card-front" aria-label="Card front">
  <div class="brand">
    <span class="brand-dot"></span>
    <div class="brand-name">THE HARBOURVIEW<br>MOTION CLINIC</div>
  </div>

  <div class="person">
    <div class="person-name">ALEX MORETON</div>
    <div class="person-title">CEO/FOUNDER</div>
  </div>

  <div class="divider"></div>

  <ul class="contacts">
    <li><svg viewBox="0 0 16 16"><path d="M3.6 1l2.3 2.8-1.2 1.8c.9 2 2.4 3.5 4.3 4.4l1.8-1.2 2.8 2.3-1.3 2.6C7 13.5 2.5 9 1.2 2.3z"/></svg>555 014 2290</li>
    <li><svg viewBox="0 0 16 16"><path d="M1 3h14v10H1z M1.8 3.8L8 8.6l6.2-4.8" fill="none" stroke="#0d56a6" stroke-width="1.6"/></svg>alex@harbourviewmotion.com</li>
    <li><svg viewBox="0 0 16 16"><rect x="1" y="1" width="14" height="14" rx="1"/></svg>/harbourviewmotion</li>
    <li><svg viewBox="0 0 16 16"><rect x="1" y="1" width="14" height="14" rx="1"/></svg>@harbourviewmotion</li>
  </ul>

  <div class="address">
    42 Seabreeze Parade<br>
    Dee Why NSW 2099<br>
    www.harbourviewmotion.com
  </div>

  <div class="base-band"></div>
</section>

<section class="card card-back" aria-label="Card back">
  <div class="faint-mark"></div>

  <div class="slot slot-row-1">Date<span class="blank blank-date"></span>Time<span class="blank blank-time"></span>am/pm</div>
  <div class="slot slot-row-2">Date<span class="blank blank-date"></span>Time<span class="blank blank-time"></span>am/pm</div>

  <div class="write-line" style="top:139px"></div>
  <div class="write-line" style="top:179px"></div>
  <div class="write-line" style="top:219px"></div>
  <div class="write-line" style="top:259px"></div>
  <div class="write-line" style="top:299px"></div>
</section>

</body>
</html>
```